Media Services Start-up -- Corporate Website and Logo Design. Inspiration required!

We need a logo design and corporate website design, including coding, for our start-up business.
Vennatra’s value proposition is based on bringing together media content from a vast number of geographies globally, adding human and AI curation, translation and editing, and delivering the content using tailored customer interfaces. On the one hand, the business brings together media coverage from all over the world, and on the other it brings together content, human skills and technology to deliver a supreme customer experience.
Vennatra is a B2B media monitoring and analytics business with emphasis on global customers. Vennatra's service offering is centred around sourcing media content from different markets, processing, storing and delivering the content and insights derived from it using an online platform / mobile app.
The messaging we want to create through the logo is:
- Global scope
- Speed of delivery
- Cost-efficiency
- Multi-lingual
- Tailor-made
- Trustworthy
Target Market(s)
Business to business, PR / Communications, Media, Marketing
Logo Text
Vennatra
Coding
Coded - Design and coding required
Number of Pages Required
5+ page
Font styles to use
Other font styles liked:
- See Design Brief for details
Colors
Designer to choose colors to be used in the design.

```html
<!DOCTYPE html>
<html lang="en">
<head>
<meta charset="utf-8">
<title>Vennatra – Global Media Intelligence</title>
<link rel="stylesheet" href="https://fonts.googleapis.com/css2?family=Arimo:wght@400;700&family=Montserrat:wght@800;900&family=Rubik:wght@400;500;600;700&display=swap">
<style>
:root{
  --backdrop:#d9d9db;
  --white:#ffffff;
  --ink:#2b2b2b;
  --body:#555a63;
  --heading:#3b4766;
  --blue:#2a56d4;
  --teal:#1ebdc1;
  --accent:#2f6fd6;
  --band:#f3f3f4;
  --line:#dcdfe4;
  --grad:linear-gradient(90deg,var(--blue),var(--teal));
}
*{box-sizing:border-box;margin:0;padding:0}
html,body{width:1200px;height:3024px;overflow:hidden}
body{background:var(--backdrop);font-family:"Arimo",Arial,sans-serif;color:var(--ink);position:relative}
.page{position:absolute;left:76px;width:1048px;background:var(--white);box-shadow:0 4px 14px rgba(0,0,0,.18);overflow:hidden}
.page--home{top:65px;height:630px}
.page--solutions{top:753px;height:2186px}

/* header */
.site-header{position:relative;height:63px;background:var(--white)}
.brand{position:absolute;left:151px;top:14px;display:flex;align-items:center;gap:7px;font-family:"Rubik",sans-serif;font-weight:600;font-size:29px;color:var(--heading);letter-spacing:-.5px}
.brand__dot{width:12px;height:12px;border-radius:50%;background:var(--accent)}
.main-nav{position:absolute;top:25px;left:335px;width:380px;height:14px}
.main-nav a{position:absolute;top:0;font-size:11px;color:var(--ink);text-decoration:none;white-space:nowrap}
.main-nav a.is-active{color:var(--accent)}
.main-nav .nav-home{left:0}
.main-nav .nav-solutions{left:55px}
.main-nav .nav-how{left:125px}
.main-nav .nav-people{left:218px}
.main-nav .nav-tech{left:299px}
.contact{position:absolute;left:737px;top:16px;display:flex;align-items:center;gap:8px}
.contact__icon{width:29px;height:29px;border-radius:50%;background:var(--grad);display:flex;align-items:center;justify-content:center}
.contact__label{font-size:8.5px;color:var(--ink);line-height:1}
.contact__number{font-family:"Rubik",sans-serif;font-weight:600;font-size:15.5px;color:var(--accent);margin-top:3px;letter-spacing:.3px}

/* hero home */
.hero{position:absolute;left:0;top:63px;width:1048px;height:520px;background:radial-gradient(ellipse at 30% 40%,#2c4a66 0%,#16283a 45%,#07090d 80%)}
.hero__title{position:absolute;left:150px;top:164px;font-family:"Montserrat",sans-serif;font-weight:900;font-size:29px;line-height:33px;color:var(--white);letter-spacing:.5px}
.hero__text{position:absolute;left:150px;top:242px;width:365px;font-size:11px;line-height:17.6px;color:var(--white)}
.lead-card{position:absolute;left:652px;top:170px;width:245px;height:259px;background:var(--white);border-radius:20px;padding:34px 18px 0}
.lead-card__title{font-family:"Rubik",sans-serif;font-weight:500;font-size:14px;color:var(--ink);text-align:center;margin-bottom:18px}
.field{height:32px;border:1px solid var(--line);border-radius:3px;margin-bottom:9px;display:flex;align-items:center;justify-content:space-between;padding:0 10px;font-size:10px;color:#8a8f97}
.btn{margin-top:5px;height:31px;border-radius:16px;background:var(--grad);color:var(--white);font-family:"Arimo",sans-serif;font-weight:700;font-size:10px;display:flex;align-items:center;justify-content:center;box-shadow:0 3px 6px rgba(42,86,212,.3)}
.wave{position:absolute;left:0;width:1048px;height:70px}

/* footer */
.site-footer{position:absolute;left:0;width:1048px;height:83px}
.site-footer__legal{position:absolute;left:151px;font-size:9.5px;color:var(--ink)}
.social{position:absolute;left:776px;display:flex;gap:5px}
.social span{width:26px;height:26px;border-radius:50%;background:var(--grad)}

/* solutions */
.banner{position:absolute;left:0;top:63px;width:1048px;height:282px;background:linear-gradient(100deg,#2b52d6 0%,#2a77d8 45%,#1fb8c3 100%)}
.banner__title{position:absolute;left:0;right:0;top:99px;text-align:center;font-family:"Montserrat",sans-serif;font-weight:900;font-size:33px;color:var(--white);letter-spacing:1px}
.service{position:absolute;left:0;width:1048px}
.service--band{background:var(--band)}
.photo{position:absolute;width:223px;height:223px;border-radius:50%;border:4px solid var(--white);box-shadow:-3px 6px 0 var(--accent)}
.photo--left{left:156px}
.photo--right{left:638px}
.copy{position:absolute}
.copy--right{left:410px}
.copy--left{left:150px}
.copy h2{font-family:"Rubik",sans-serif;font-weight:500;font-size:21px;color:var(--heading);margin-bottom:13px}
.copy p{font-size:10.5px;line-height:17.6px;color:var(--body);margin-bottom:8px}
.copy ul{list-style:none}
.copy li{position:relative;padding-left:18px;font-size:10.5px;line-height:17.6px;color:var(--body);margin-bottom:8px}
.copy li::before{content:"";position:absolute;left:0;top:4px;width:9px;height:9px;border-radius:50%;border:2px solid var(--accent)}
</style>
</head>
<body>

<!-- Home page -->
<section class="page page--home">
  <header class="site-header">
    <div class="brand"><span class="brand__dot"></span>Vennatra</div>
    <nav class="main-nav">
      <a class="nav-home">Home</a><a class="nav-solutions">Solutions</a><a class="nav-how">How We Do It</a><a class="nav-people">Our People</a><a class="nav-tech">Our Technology</a>
    </nav>
    <div class="contact">
      <div class="contact__icon"><svg width="12" height="12" viewBox="0 0 24 24"><path fill="#fff" d="M6.6 10.8a15 15 0 006.6 6.6l2.2-2.2c.3-.3.7-.4 1-.2 1.1.4 2.3.6 3.6.6.6 0 1 .4 1 1V20c0 .6-.4 1-1 1A17 17 0 013 4c0-.6.4-1 1-1h3.5c.6 0 1 .4 1 1 0 1.3.2 2.5.6 3.6.1.3 0 .7-.2 1z"/></svg></div>
      <div><div class="contact__label">Talk to us today</div><div class="contact__number">(00) 5820 4417</div></div>
    </div>
  </header>

  <div class="hero" role="img" aria-label="Person facing a curved wall of glowing media screens in a dark room">
    <h1 class="hero__title">DELIVERING GLOBAL<br>MEDIA INTELLIGENCE</h1>
    <p class="hero__text">Vennatra is an international media intelligence service provider. We help communications teams build and operate truly global media monitoring and measurement programmes.</p>
    <form class="lead-card">
      <div class="lead-card__title">Learn more about Vennatra</div>
      <div class="field">Name:<svg width="8" height="9" viewBox="0 0 8 9"><circle cx="4" cy="2.3" r="2.1" fill="#aaa"/><path d="M0 9a4 3.5 0 018 0z" fill="#aaa"/></svg></div>
      <div class="field">Email:<svg width="9" height="7" viewBox="0 0 9 7"><rect width="9" height="7" fill="#aaa"/><path d="M0 0l4.5 3.5L9 0" stroke="#fff" fill="none"/></svg></div>
      <div class="field">Phone:<svg width="8" height="8" viewBox="0 0 24 24"><path fill="#aaa" d="M6.6 10.8a15 15 0 006.6 6.6l2.2-2.2c.3-.3.7-.4 1-.2 1.1.4 2.3.6 3.6.6.6 0 1 .4 1 1V20c0 .6-.4 1-1 1A17 17 0 013 4c0-.6.4-1 1-1h3.5c.6 0 1 .4 1 1 0 1.3.2 2.5.6 3.6.1.3 0 .7-.2 1z"/></svg></div>
      <div class="btn">GET STARTED</div>
    </form>
  </div>
  <svg class="wave" style="top:513px" viewBox="0 0 1048 70" preserveAspectRatio="none">
    <defs><linearGradient id="waveA" x1="0" x2="1"><stop offset="0" stop-color="#2a56d4"/><stop offset=".5" stop-color="#1fb8c3"/><stop offset="1" stop-color="#2a56d4"/></linearGradient></defs>
    <path d="M0 56C320 26 700 -4 1048 16L1048 70 0 70Z" fill="url(#waveA)"/>
    <path d="M0 57C330 34 720 18 1048 40L1048 70 0 70Z" fill="#fff"/>
  </svg>
  <footer class="site-footer" style="top:583px;background:#fff">
    <div class="site-footer__legal" style="top:20px">© 2019 All Rights Are Reserved. Terms of Use | Privacy Policy</div>
    <div class="social" style="top:5px"><span></span><span></span><span></span><span></span></div>
  </footer>
</section>

<!-- Solutions page -->
<section class="page page--solutions">
  <header class="site-header">
    <div class="brand"><span class="brand__dot"></span>Vennatra</div>
    <nav class="main-nav">
      <a class="nav-home">Home</a><a class="nav-solutions is-active">Solutions</a><a class="nav-how">How We Do It</a><a class="nav-people">Our People</a><a class="nav-tech">Our Technology</a>
    </nav>
    <div class="contact">
      <div class="contact__icon"><svg width="12" height="12" viewBox="0 0 24 24"><path fill="#fff" d="M6.6 10.8a15 15 0 006.6 6.6l2.2-2.2c.3-.3.7-.4 1-.2 1.1.4 2.3.6 3.6.6.6 0 1 .4 1 1V20c0 .6-.4 1-1 1A17 17 0 013 4c0-.6.4-1 1-1h3.5c.6 0 1 .4 1 1 0 1.3.2 2.5.6 3.6.1.3 0 .7-.2 1z"/></svg></div>
      <div><div class="contact__label">Talk to us today</div><div class="contact__number">(00) 5820 4417</div></div>
    </div>
  </header>

  <div class="banner" role="img" aria-label="Blue-tinted wall of media screens">
    <h1 class="banner__title">SOLUTIONS</h1>
  </div>
  <svg class="wave" style="top:283px" viewBox="0 0 1048 70" preserveAspectRatio="none">
    <defs><linearGradient id="waveB" x1="0" x2="1"><stop offset="0" stop-color="#2a56d4"/><stop offset=".5" stop-color="#1fb8c3"/><stop offset="1" stop-color="#2a56d4"/></linearGradient></defs>
    <path d="M0 56C320 26 700 -4 1048 16L1048 70 0 70Z" fill="url(#waveB)"/>
    <path d="M0 57C330 34 720 18 1048 40L1048 70 0 70Z" fill="#fff"/>
  </svg>

  <article class="service" style="top:345px;height:341px">
    <div class="photo photo--left" style="top:59px;background:radial-gradient(circle at 65% 55%,#c7922f,#6b5a4a 55%,#cfd4da)" role="img" aria-label="Analyst working at a monitor"></div>
    <div class="copy copy--right" style="top:50px;width:450px">
      <h2>Content Sourcing</h2>
      <p>We help you build a content strategy that meets your budget and coverage needs across earned media - Print, Online, TV and Radio.</p>
      <ul>
        <li>Identify geographies and markets of interest</li>
        <li>Build target media source lists to fulfil monitoring and measurement requirements</li>
        <li>Using our transparent cost calculator, we help you with accurate budgeting and choices to ensure you meet your strategy and objectives</li>
        <li>Translate and localise keyword searches and editorial instructions into effecient source-/ country-/ provider-specific needs to minimise wasted content.</li>
      </ul>
    </div>
  </article>

  <article class="service service--band" style="top:686px;height:334px">
    <div class="copy copy--left" style="top:103px;width:440px">
      <h2>Content Collection</h2>
      <ul><li>We consolidate and manage the delivery of your global media content into a Cloud-based scalable media platform, taking the headache of content management away from your teams.</li></ul>
    </div>
    <div class="photo photo--right" style="top:53px;background:radial-gradient(circle at 60% 45%,#a3866d,#4a3a35 55%,#7b8590)" role="img" aria-label="Engineer at a broadcast mixing desk"></div>
  </article>

  <article class="service" style="top:1020px;height:370px">
    <div class="photo photo--left" style="top:61px;background:radial-gradient(circle at 50% 60%,#c9d1dc,#6f6660 55%,#2e2a2a)" role="img" aria-label="Hands using a smartphone"></div>
    <div class="copy copy--right" style="top:58px;width:515px">
      <h2>Content Augmentation</h2>
      <ul>
        <li>We manage and normalise all of the source-level reference data - country, language, reach etc.</li>
        <li>We add editorial validation to ensure only the content required reaches your delivery, removing inevitable noise from source providers</li>
        <li>Tagging - AI and human based tagging to detect locations, people, topics, products, brands, services, etc.</li>
        <li>Human and automated grouping of stories across geographies - clustering, "also-in" groupings etc.</li>
        <li>Translation summarisation - AI Translation or human-created depending on budget, speed of delivery and need.</li>
        <li>Digest authoring - refining the essence of today's coverage into a concise board-ready output for your organisation</li>
      </ul>
    </div>
  </article>

  <article class="service service--band" style="top:1390px;height:332px">
    <div class="copy copy--left" style="top:66px;width:450px">
      <h2>Content Delivery</h2>
      <p style="margin-bottom:14px">Early morning delivery of a consolidated, ready-to-consume media coverage</p>
      <ul>
        <li>Customised email templates, delivering content in templates designed to meet your needs</li>
        <li>Customised platform - modern portal tailored to meet your media management needs, removing the unwanted clutter and focusing on the job at hand.</li>
        <li>Integration with Intranets, third-party communication tools e.g. chat apps, RSS readers, customised APIs</li>
      </ul>
    </div>
    <div class="photo photo--right" style="top:52px;background:radial-gradient(circle at 40% 35%,#e0a767,#8c5a3c 50%,#2b2a2e)" role="img" aria-label="Camera on a desk in warm studio light"></div>
  </article>

  <article class="service" style="top:1722px;height:381px">
    <div class="photo photo--left" style="top:78px;background:radial-gradient(circle at 55% 45%,#3c4f7a,#17203a 60%,#8ea0c4)" role="img" aria-label="Broadcast video camera in blue light"></div>
    <div class="copy copy--right" style="top:88px;width:480px">
      <h2>Media Insights &amp; Consultancy</h2>
      <ul>
        <li>Levering the normalised content sets from your integrated monitoring service, we can analyse and tag your coverage based on complex qualitative measurement criteria, consistent across all languages and geographies, to combine with quantitative metrics.</li>
        <li>Consultancy to HQ and local offices on how to utilise and align existing measurement and insight intiatives to provide continuity.</li>
        <li>Customised online dashboards with near real time data insights, coupled with Board-ready offline reporting and export options.</li>
        <li>Integration with social media content, third-party data, point-of-sale, web analytics, and delivering on your Integrated Communications Framework</li>
      </ul>
    </div>
  </article>

  <footer class="site-footer" style="top:2103px;background:var(--band)">
    <div class="site-footer__legal" style="top:41px">© 2019 All Rights Are Reserved. Terms of Use | Privacy Policy</div>
    <div class="social" style="top:33px"><span></span><span></span><span></span><span></span></div>
  </footer>
</section>

</body>
</html>
```